Trucking Company Website Design

We are working with a Trucking company in California. They provide trucking services for dirt, gravel, landscape bark, and landscape materials.

As you might imagine, there are no websites we could find for inspiration for trucking companies.

Thank you for taking the time to consider designing a website for us. We are web developers based in Stockton, CA, USA. Most of our projects go through the same process. Understanding this process may help you win a project with us. We custom-code all of our websites in-house. We don’t have any requirements as to what tools you use for your design, but we ask that you follow these guidelines.

IMAGES:
If you use any images or icons in the design, we ask that you have a link to the asset so we can purchase the image/icon. Most of the designs we submit do not have the customer’s images on them unless they have some great images. Be creative; show us the feeling you are trying to portray with your image choices. Use any royalty-free site you choose. We subscribe to Quillo and mainly use their images, but we can purchase images outside of Quillo. PLEASE NOTE: we will not submit designs to clients with watermarks on the images.

FONTS:
We ask that you identify the fonts you’re using in the design. This can be done in a message if you want. We typically use Varnex Fonts and Quillo Fonts.

CONTENT:
We're always open to different content and ideas. We often submit designs with stock images so the client can see our vision. We typically take pictures after the website launch to use their images with our vision. Lorem Ipsum is fine for paragraphs, but we ask that you make the Headers with correct English. We want to be able to show the vision and identify the sections of the website.

INSPIRATION:
We typically add a couple of links in the brief of websites we like to help you get started in your design.

REVISIONS:
We do not often ask for revisions of the designs unless we see something in the design that may not appeal to the client. If there are slight changes that we want to make, we do that in the development process.

FEEDBACK:
We rarely give feedback on designs during the design process. We are working on many website projects and do not have the time to provide feedback. We usually respond if your request is well thought out and asks specific questions, but a note asking “feedback, please” usually goes unanswered.

```html
<!DOCTYPE html>
<html lang="en">
<head>
<meta charset="utf-8">
<title>Harlow Materials – Trucking</title>
<link href="https://fonts.googleapis.com/css2?family=Barlow:wght@400;500;600;700&display=swap" rel="stylesheet">
<style>
:root{
  --navy:#0b2335;
  --red:#ee3124;
  --blue:#0a8cc6;
  --ink:#222;
  --grey:#666;
  --light:#f3f3f3;
  --footer:#141414;
  --white:#fff;
}
*{box-sizing:border-box;margin:0;padding:0}
html,body{width:1200px;height:4256px;overflow:hidden}
body{position:relative;font-family:'Barlow',sans-serif;color:var(--ink);background:var(--white)}
.abs{position:absolute}
.photo{position:absolute;display:block}
/* header */
.site-header{position:absolute;left:0;top:0;width:1200px;height:86px;background:var(--white)}
.brand{position:absolute;display:flex;align-items:center;gap:10px;font-weight:700;font-size:20px;color:var(--blue);letter-spacing:.3px;line-height:1;white-space:nowrap}
.brand-mark{width:26px;height:26px;background:var(--red)}
.site-header .brand{left:111px;top:30px}
.main-nav{position:absolute;left:408px;top:33px;font-size:14px;font-weight:500;color:#333}
.main-nav a{color:inherit;text-decoration:none;position:absolute;white-space:nowrap}
.main-nav .active{color:var(--red)}
.main-nav .active::after{content:"";position:absolute;left:0;right:0;top:50px;height:3px;background:var(--red)}
.call-btn{position:absolute;left:853px;top:12px;width:235px;height:62px;background:var(--red);clip-path:polygon(0 0,92% 0,100% 50%,92% 100%,0 100%);color:var(--white)}
.call-btn .icon{position:absolute;left:16px;top:14px;width:34px;height:34px;border-radius:50%;background:var(--white)}
.call-btn small{position:absolute;left:58px;top:10px;font-size:13px}
.call-btn strong{position:absolute;left:58px;top:28px;font-size:20px;font-weight:700;white-space:nowrap}
/* hero */
.hero{position:absolute;left:0;top:86px;width:1200px;height:643px;background:var(--navy);overflow:hidden}
.hero h1{position:absolute;left:111px;top:210px;width:440px;font-size:44px;line-height:51px;font-weight:700;color:var(--white);text-transform:uppercase}
.btn{display:inline-block;font-weight:700;text-transform:uppercase;font-size:13px;text-decoration:none}
.btn-red{background:var(--red);color:var(--white)}
.hero .btn{position:absolute;left:111px;top:380px;width:145px;height:40px;line-height:40px;text-align:center}
.slider-dot{position:absolute;top:515px;width:50px;height:50px;border-radius:50%;background:var(--white)}
/* about */
.about h2,.section-title{font-weight:700;text-transform:uppercase;color:var(--ink)}
.about h2{position:absolute;left:635px;top:822px;font-size:42px}
.about p{position:absolute;left:634px;width:455px;font-size:13.5px;line-height:25.6px;color:var(--grey);text-align:justify}
.about .btn{position:absolute;left:633px;top:1241px;width:146px;height:40px;line-height:40px;text-align:center}
/* services */
.services{position:absolute;left:0;top:1382px;width:1200px;height:1169px;background:var(--light)}
.section-title{position:absolute;left:0;width:1200px;text-align:center;font-size:42px}
.service-card{position:absolute;width:474px;height:433px}
.service-card .label{position:absolute;left:44px;top:269px;width:387px;height:133px;background:var(--white);text-align:center}
.service-card .badge{position:absolute;left:143px;top:-52px;width:102px;height:102px;border-radius:50%;background:var(--white)}
.service-card .badge svg{position:absolute;left:31px;top:33px}
.service-card h3{position:absolute;left:0;right:0;top:70px;font-size:20px;font-weight:600;letter-spacing:.5px;text-transform:uppercase}
/* project */
.project{position:absolute;left:0;top:2551px;width:1200px;height:593px;background:var(--blue)}
.project-card{position:absolute;left:111px;top:76px;width:489px;height:441px;background:var(--red);border-radius:16px;color:var(--white);text-align:center}
.project-card h2{margin-top:38px;font-size:42px;font-weight:700;text-transform:uppercase}
.project-card p{margin:8px 44px 0;font-size:15px;line-height:25.6px;text-align:justify;text-align-last:center}
.project-card .btn{margin-top:20px;width:170px;height:40px;line-height:40px;background:var(--white);color:var(--ink)}
/* blog */
.blog-card{position:absolute;top:3316px;width:310px;height:463px;background:var(--white);box-shadow:0 6px 22px rgba(0,0,0,.08);text-align:center}
.blog-card .date{position:absolute;left:91px;top:193px;width:130px;height:38px;line-height:38px;background:var(--blue);color:var(--white);font-size:12px;font-weight:700}
.blog-card h3{position:absolute;left:40px;right:40px;top:262px;font-size:20px;line-height:28px;font-weight:600}
.blog-card p{position:absolute;left:30px;right:30px;top:334px;font-size:12px;line-height:20px;color:#888}
.blog-card a{position:absolute;left:0;right:0;top:410px;font-size:13px;font-weight:600;color:var(--red);text-decoration:underline;text-transform:uppercase}
.blog-arrow{position:absolute;top:3532px;width:40px;height:40px;border-radius:50%;background:#e6e6e6;color:#555;text-align:center;line-height:38px;font-size:14px}
/* footer */
.site-footer{position:absolute;left:0;top:3889px;width:1200px;height:367px;background:var(--footer);color:var(--white)}
.site-footer .brand{left:111px;top:88px}
.social{position:absolute;top:162px;width:24px;height:24px;border-radius:50%;background:var(--white)}
.footer-col{position:absolute;top:76px}
.footer-col h4{font-size:24px;font-weight:700;text-transform:uppercase;margin-bottom:12px;white-space:nowrap}
.footer-col li{list-style:none;font-size:13px;line-height:26px;padding-left:26px;position:relative;white-space:nowrap}
.footer-col li::before{content:"»";position:absolute;left:0;top:-1px}
.footer-col.contact li::before{content:"";width:8px;height:8px;top:9px;background:var(--red);border-radius:50%}
.footer-rule{position:absolute;left:74px;top:277px;width:1052px;border-top:2px dotted #bbb}
.copyright{position:absolute;left:0;width:1200px;top:313px;text-align:center;font-size:12px}
</style>
</head>
<body>

<header class="site-header">
  <div class="brand"><span>HARLOW MATERIALS</span><span class="brand-mark"></span></div>
  <nav class="main-nav">
    <a class="active" style="left:0">Home</a>
    <a style="left:63px">About</a>
    <a style="left:128px">Services</a>
    <a style="left:209px">Project</a>
    <a style="left:281px">Reviews</a>
    <a style="left:361px">Contact</a>
  </nav>
  <div class="call-btn">
    <span class="icon"><svg width="34" height="34" viewBox="0 0 34 34"><path d="M11 9c1-1 2-1 3 0l2 3c.6 1 .3 2-.5 2.6l-1 .8c.8 2 2.4 3.6 4.4 4.4l.8-1c.6-.8 1.6-1.1 2.6-.5l3 2c1 1 1 2 0 3l-1.5 1.5C19 26 8 15 9.5 10.5z" fill="#ee3124"/></svg></span>
    <small>Call Us :</small>
    <strong>+1 555 014 2290</strong>
  </div>
</header>

<section class="hero">
  <div class="photo" role="img" aria-label="Faint dotted world map" style="left:190px;top:150px;width:380px;height:360px;background:radial-gradient(ellipse at center,rgba(255,255,255,.06),transparent 70%)"></div>
  <div class="abs" style="left:408px;top:506px;width:792px;height:137px;background:var(--blue)"></div>
  <div class="abs" style="left:593px;top:66px;width:513px;height:577px;background:var(--red)"></div>
  <div class="photo" role="img" aria-label="White semi truck driving on a highway at sunset" style="left:577px;top:83px;width:512px;height:560px;background:linear-gradient(180deg,#6d8fb4 0%,#a9b6c4 38%,#e8b979 52%,#6a6b70 62%,#3f4248 100%)"></div>
  <h1>Transport your goods around the world</h1>
  <a class="btn btn-red">Get Started</a>
  <span class="slider-dot" style="left:111px"><svg width="50" height="50"><path d="M28 19l-6 6 6 6" fill="none" stroke="#222" stroke-width="2"/></svg></span>
  <span class="slider-dot" style="left:170px"><svg width="50" height="50"><path d="M22 19l6 6-6 6" fill="none" stroke="#222" stroke-width="2"/></svg></span>
</section>

<section class="about">
  <svg class="abs" style="left:111px;top:833px" width="395" height="425"><path d="M355 86h30v55M95 385v37h85" fill="none" stroke="#ee3124" stroke-width="4"/></svg>
  <div class="photo" role="img" aria-label="Palm plant over gravel and green lawn" style="left:111px;top:833px;width:350px;height:385px;background:linear-gradient(160deg,#4f8a2a 0%,#7fb83a 40%,#c7b89a 60%,#a38d6c 100%)"></div>
  <div class="photo" role="img" aria-label="Modern house with landscaped front yard at dusk" style="left:293px;top:980px;width:266px;height:293px;border:6px solid #fff;background:linear-gradient(180deg,#d98a7c 0%,#8a8fa6 40%,#4d4d55 62%,#4b7d2c 100%)"></div>
  <h2>About Us</h2>
  <p style="top:886px">Lorem ipsum dolor sit amet, consectetur adipiscing elit, sed do eiusmod tempor incididunt ut labore et dolore magna aliqua. Ut enim ad minim veniam, quis nostrud exercitation ullamco laboris nisi ut aliquip ex ea commodo consequat. Duis aute irure dolor in reprehenderit in voluptate velit esse cillum dolore eu fugiat nulla pariatur.</p>
  <p style="top:1040px">Excepteur sint occaecat cupidatat non proident, sunt in culpa qui officia deserunt mollit anim id est laborum. Lorem ipsum dolor sit amet, consectetur adipiscing elit, sed do eiusmod tempor incididunt ut labore et dolore magna aliqua. Ut enim ad minim veniam, quis nostrud exercitation ullamco laboris nisi ut aliquip ex ea commodo consequat. Duis aute irure dolor in reprehenderit in voluptate velit esse cillum dolore eu fugiat nulla pariatur.</p>
  <a class="btn btn-red">Learn More ›</a>
</section>

<section class="services">
  <h2 class="section-title" style="top:93px">Our Services</h2>

  <article class="service-card" style="left:111px;top:172px">
    <div class="photo" role="img" aria-label="Orange dump truck under a cloudy sky" style="inset:0;background:linear-gradient(180deg,#8a8f96 0%,#b98360 45%,#3b3b3b 100%)"></div>
    <div class="label"><span class="badge"><svg width="40" height="36"><path d="M2 30L16 10l6 6 4-4 12 18z" fill="none" stroke="#ee3124" stroke-width="2"/><path d="M2 33h36" stroke="#0a8cc6" stroke-width="2"/></svg></span><h3>Dirt</h3></div>
  </article>

  <article class="service-card" style="left:615px;top:172px">
    <div class="photo" role="img" aria-label="Tipper truck unloading gravel" style="inset:0;background:linear-gradient(180deg,#6fa3d8 0%,#c7986a 45%,#9a948c 100%)"></div>
    <div class="label"><span class="badge"><svg width="40" height="36"><path d="M4 30L20 6l16 24z" fill="none" stroke="#ee3124" stroke-width="2"/><path d="M2 33h36" stroke="#0a8cc6" stroke-width="2"/><circle cx="20" cy="20" r="2" fill="#0a8cc6"/><circle cx="14" cy="26" r="2" fill="#0a8cc6"/><circle cx="26" cy="26" r="2" fill="#0a8cc6"/></svg></span><h3>Gravel</h3></div>
  </article>

  <article class="service-card" style="left:111px;top:633px">
    <div class="photo" role="img" aria-label="Wheelbarrow of bark mulch in a garden bed" style="inset:0;background:linear-gradient(180deg,#e6e2d8 0%,#9b6a3e 40%,#4e3826 70%,#4f7a2d 100%)"></div>
    <div class="label"><span class="badge"><svg width="40" height="36"><path d="M12 4l8 14H4zM28 8l8 14H20z" fill="none" stroke="#ee3124" stroke-width="2"/><path d="M2 30h36M6 34h28" stroke="#0a8cc6" stroke-width="2"/></svg></span><h3>Landscape Bark</h3></div>
  </article>

  <article class="service-card" style="left:615px;top:633px">
    <div class="photo" role="img" aria-label="Roll of fresh sod being laid on soil" style="inset:0;background:linear-gradient(180deg,#6d9c3e 0%,#c9c0a4 35%,#7d6a4d 65%,#4a3a2a 100%)"></div>
    <div class="label"><span class="badge"><svg width="40" height="36"><circle cx="8" cy="8" r="3" fill="none" stroke="#ee3124" stroke-width="2"/><path d="M4 30l10-12 6 6 6-10 10 16z" fill="none" stroke="#0a8cc6" stroke-width="2"/><path d="M2 33h36" stroke="#ee3124" stroke-width="2"/></svg></span><h3>Landscape Materials</h3></div>
  </article>
</section>

<section class="project">
  <div class="photo" role="img" aria-label="Blue-roofed country house with a green lawn" style="left:428px;top:0;width:772px;height:593px;background:linear-gradient(180deg,#4f6f8c 0%,#8fa2ad 45%,#7e8f98 62%,#4e7a32 80%,#3c5f22 100%)"></div>
  <div class="project-card">
    <h2>Our Project</h2>
    <p>Lorem ipsum dolor sit amet, consectetur adipiscing elit, sed do eiusmod tempor incididunt ut labore et dolore magna aliqua. Ut enim ad minim veniam, quis nostrud exercitation ullamco laboris nisi ut aliquip ex ea commodo consequat. Duis aute irure dolor in reprehenderit in voluptate velit esse cillum dolore eu fugiat nulla pariatur. Excepteur sint occaecat cupidatat non proident, sunt in culpa qui officia deserunt mollit anim id est laborum.</p>
    <a class="btn">View Our Project</a>
  </div>
</section>

<section class="blog">
  <h2 class="section-title" style="top:3236px">Our Latest Blog</h2>
  <span class="blog-arrow" style="left:35px">‹</span>
  <span class="blog-arrow" style="left:1124px">›</span>

  <article class="blog-card" style="left:111px">
    <div class="photo" role="img" aria-label="Trucks on a highway with sun through clouds" style="left:0;top:0;width:310px;height:231px;background:linear-gradient(180deg,#3c6fb0 0%,#c9d3dd 45%,#6c7a4a 70%,#555 100%)"></div>
    <span class="date">▦ APR 19,2023</span>
    <h3>Lorem ipsum dolor sit amet, consectetur</h3>
    <p>Lorem ipsum dolor sit amet, consectetur adipiscing elit, sed do eiusmod tempor incididunt ut labore</p>
    <a>Learn More ›</a>
  </article>

  <article class="blog-card" style="left:446px">
    <div class="photo" role="img" aria-label="Red truck on a tree-lined road" style="left:0;top:0;width:310px;height:231px;background:linear-gradient(180deg,#5d8fc8 0%,#cfd9e2 35%,#4c7a34 60%,#777 100%)"></div>
    <span class="date">▦ APR 19,2023</span>
    <h3>Lorem ipsum dolor sit amet, consectetur</h3>
    <p>Lorem ipsum dolor sit amet, consectetur adipiscing elit, sed do eiusmod tempor incididunt ut labore</p>
    <a>Learn More ›</a>
  </article>

  <article class="blog-card" style="left:779px">
    <div class="photo" role="img" aria-label="Truck on a rural highway at dusk" style="left:0;top:0;width:310px;height:231px;background:linear-gradient(180deg,#41638c 0%,#e0b77c 40%,#587a36 65%,#3d5c2a 100%)"></div>
    <span class="date">▦ APR 19,2023</span>
    <h3>Lorem ipsum dolor sit amet, consectetur</h3>
    <p>Lorem ipsum dolor sit amet, consectetur adipiscing elit, sed do eiusmod tempor incididunt ut labore</p>
    <a>Learn More ›</a>
  </article>
</section>

<footer class="site-footer">
  <div class="brand"><span>HARLOW MATERIALS</span><span class="brand-mark"></span></div>
  <span class="social" style="left:125px"></span>
  <span class="social" style="left:155px"></span>
  <span class="social" style="left:185px"></span>
  <span class="social" style="left:216px"></span>

  <div class="footer-col" style="left:385px">
    <h4>Our Services</h4>
    <ul><li>Dirt</li><li>Gravel</li><li>Landscape bark</li><li>Landscape materials.</li></ul>
  </div>
  <div class="footer-col" style="left:643px">
    <h4>Quick Links</h4>
    <ul><li>Home</li><li>About</li><li>Services</li><li>Contact</li></ul>
  </div>
  <div class="footer-col contact" style="left:866px">
    <h4>Contact Us</h4>
    <ul><li>123,Lorem ipsum dolor sit amet</li><li>+1 555 014 2290</li><li>hello@harlowmaterials.com</li></ul>
  </div>
  <div class="footer-rule"></div>
  <p class="copyright">© Copyrights 2023 | All Rights Reserved</p>
</footer>

</body>
</html>
```